Redesign of LumoWordfind.com in Bootstrap 4

Current design of LumoWordfind.com is not responsive. We need to change it to latest version of Bootstrap 4 keeping essential elements in place.

Apart from home page, we need designs for http://www.lumowordfind.com/meaning/cat also.

Coding

Number of Pages Required

2 page

Colors
34a7d8

Requirements
Must have
• Bootstrap 4

```html
<!DOCTYPE html>
<html lang="en">
<head>
<meta charset="utf-8">
<title>Lumo Wordfind – Search, Save and Master Words</title>
<link href="https://fonts.googleapis.com/css2?family=Open+Sans:wght@400;600;700&family=Raleway:wght@400;500;600&family=Poiret+One&display=swap" rel="stylesheet">
<style>
:root{
  --brand:#34a7d8;
  --brand-band:#2f9bd3;
  --ink:#222;
  --topbar:#252525;
  --dark:#1c1c1c;
  --nav:#1f1f1f;
  --page:#e4ebf1;
  --tidbit:#e2edd1;
  --tidbit-foot:#e8eaea;
  --muted:#7a7a7a;
  --accent:#f39c12;
  --white:#fff;
}
*{box-sizing:border-box;margin:0;padding:0}
html,body{width:820px;height:1200px;overflow:hidden}
body{position:relative;background:var(--page);font-family:'Open Sans',sans-serif;color:var(--ink)}
.topbar{position:absolute;left:0;top:0;width:820px;height:31px;background:var(--topbar)}
.social{position:absolute;left:89px;top:10px;display:flex;gap:12px}
.social span{width:10px;height:10px;border-radius:50%;background:#ddd;display:block}
.login{position:absolute;right:91px;top:7px;display:flex;align-items:center;font-size:7.5px;color:#eee}
.login label{margin-right:10px}
.login .field{width:100px;border-bottom:1px solid #777;color:#666;font-size:6px;padding-bottom:2px;margin-right:13px}
.login .btn{background:var(--brand);color:#fff;font-size:7px;padding:5px 10px}
.header{position:absolute;left:0;top:31px;width:820px;height:95px;border-bottom:1px solid #c9d2da}
.logo{position:absolute;left:90px;top:20px;font-family:'Open Sans',sans-serif;font-weight:700;font-size:22px;color:var(--ink);line-height:1}
.logo small{display:block;font-size:8.5px;letter-spacing:.6px;color:var(--ink);margin-top:2px;font-weight:700}
.join{position:absolute;right:91px;top:22px;background:var(--dark);color:var(--accent);font-family:'Raleway',sans-serif;font-size:10px;padding:5px 10px;border-radius:2px}
.nav{position:absolute;left:92px;top:69px;width:638px;display:flex;justify-content:space-between}
.nav a{width:85px;height:25px;background:var(--nav);color:#eee;font-size:8.5px;display:flex;align-items:center;justify-content:center;text-decoration:none;font-family:'Open Sans',sans-serif}
.nav a.active{background:var(--brand);color:#fff}
.hero{position:absolute;left:0;top:137px;width:820px;height:328px;background:radial-gradient(ellipse at 50% 70%,#5a3a26 0%,#2a1a12 45%,#0b0705 100%)}
.hero h1{position:absolute;top:72px;width:100%;text-align:center;font-family:'Poiret One',sans-serif;font-weight:400;font-size:28px;color:#fff}
.search{position:absolute;left:131px;top:128px;width:558px;height:48px;border:3px solid var(--brand);background:#fff;padding:3px;display:flex}
.search .input{flex:1;border:1px solid #ccc;font-size:10px;color:#999;padding:12px 11px}
.search .input i{color:#aaa}
.search .go{width:78px;background:var(--dark);color:var(--brand);font-size:10px;display:flex;align-items:center;justify-content:center}
.features{position:absolute;left:90px;top:205px;width:640px;display:grid;grid-template-columns:323px 1fr;row-gap:14px;font-size:10px;color:#eee}
.features li{list-style:none;display:flex;align-items:center;gap:6px}
.features li::before{content:"";width:8px;height:8px;border-radius:50%;background:var(--brand)}
.dots{position:absolute;left:389px;top:297px;display:flex;gap:5px}
.dots span{width:7px;height:7px;border-radius:50%;background:#fff}
.dots span:first-child{background:none;border:1.5px solid var(--brand)}
.browse{position:absolute;left:0;top:465px;width:820px;height:42px;background:var(--dark);display:flex;align-items:center;padding-left:90px}
.browse b{font-weight:400;font-size:9px;color:#eee;margin-right:12px}
.letters{display:flex;gap:3px}
.letters span{width:18px;height:18px;border:1px solid #ccc;color:#ddd;font-size:8px;display:flex;align-items:center;justify-content:center}
.letters span.on{background:var(--brand);border-color:var(--brand);color:#fff}
.crossword{position:absolute;left:90px;top:522px;width:452px;height:206px;background:linear-gradient(135deg,#3a3a3a,#1b1b1b);text-align:center;color:#fff}
.crossword h2{margin-top:60px;font-family:'Raleway',sans-serif;font-weight:500;font-size:15px;color:var(--brand)}
.crossword p{font-size:8.5px;margin-top:8px}
.crossword .btn{display:inline-block;margin-top:9px;background:#fff;color:var(--brand);font-size:9.5px;width:106px;padding:8px 0}
.tidbit{position:absolute;left:557px;top:522px;width:172px;height:206px;background:var(--tidbit)}
.tidbit h3{font-family:'Open Sans',sans-serif;font-weight:400;font-size:14px;margin:15px 0 0 19px}
.tidbit .word{font-size:12px;color:var(--brand);margin:12px 0 0 20px;font-family:'Raleway',sans-serif}
.tidbit p{font-size:8.5px;line-height:16px;color:#777;margin:10px 20px 0 20px;text-align:justify}
.tidbit .arrows{position:absolute;right:36px;top:158px;font-size:10px;font-weight:700;color:#222}
.tidbit .arrows b{color:var(--brand)}
.tidbit footer{position:absolute;left:0;bottom:0;width:100%;height:24px;background:var(--tidbit-foot);display:flex;justify-content:space-between;align-items:center;padding:0 10px;font-size:6.5px;color:#666}
.addon{position:absolute;left:90px;top:742px;width:639px;height:165px;background:var(--brand-band);text-align:center;color:#fff}
.addon h2{margin-top:24px;font-family:'Raleway',sans-serif;font-weight:500;font-size:15px}
.addon h4{margin-top:8px;font-family:'Raleway',sans-serif;font-weight:600;font-size:11.5px}
.addon p{margin:9px auto 0;width:290px;font-size:8.5px;line-height:15px;color:#eaf5fb}
.addon .btn{display:inline-block;margin-top:10px;background:var(--dark);color:#fff;font-size:9.5px;width:106px;padding:8px 0}
.press{position:absolute;left:538px;top:48px;width:76px;height:76px;border-radius:50%;background:#fff;color:#333;text-align:center}
.press::before{content:"";position:absolute;left:37px;top:-48px;width:1px;height:48px;background:#333}
.press b{display:block;margin-top:18px;font-family:'Raleway',sans-serif;font-weight:500;font-size:8.5px;letter-spacing:.5px;border-bottom:1px solid #ccc;margin-left:10px;margin-right:10px;padding-bottom:4px}
.press span{display:block;margin-top:6px;font-size:7px;color:var(--brand)}
.mobile{position:absolute;left:92px;top:925px;width:636px;height:201px;background:linear-gradient(90deg,#140c08 0%,#3c2418 40%,#2a1811 70%,#0b0705 100%);color:#fff}
.mobile .text{position:absolute;left:38px;top:54px;width:270px;text-align:center}
.mobile h2{font-family:'Open Sans',sans-serif;font-weight:400;font-size:15px}
.mobile p{font-size:8.5px;line-height:17px;margin-top:10px}
.store{display:inline-block;margin-top:12px;width:85px;height:29px;border:1px solid #999;border-radius:5px;background:#000}
.phone{position:absolute;left:390px;top:10px;width:210px;height:191px;background:linear-gradient(180deg,#8a6a55,#c99c80);opacity:.85}
.footer{position:absolute;left:0;top:1143px;width:820px;height:57px;background:#111;color:#ddd;text-align:center}
.footer nav{margin-top:16px;font-size:7.5px;display:flex;justify-content:center;gap:9px}
.footer p{margin-top:11px;font-size:7.5px}
</style>
</head>
<body>
<div class="topbar">
  <div class="social"><span></span><span></span><span></span><span></span><span></span></div>
  <div class="login">
    <label>User name :</label><div class="field">Enter user name</div>
    <label>Password :</label><div class="field">Password</div>
    <div class="btn">LOG IN</div>
  </div>
</div>

<header class="header">
  <div class="logo">Lumo<small>WORDFIND</small></div>
  <div class="join">Join for FREE!</div>
  <nav class="nav">
    <a class="active">HOME</a><a>IDIOMS</a><a>COMMON ERRORS</a><a>CROSSWORD</a><a>BLOG</a><a>CONTACT</a>
  </nav>
</header>

<section class="hero" role="img" aria-label="Photo of reading glasses resting in front of a stack of books">
  <h1>Search, Save and Master Words</h1>
  <div class="search">
    <div class="input">Enter a word or phrase &nbsp;<i>(eg. symbol, grace, explanation)</i></div>
    <div class="go">SEARCH</div>
  </div>
  <ul class="features">
    <li>Search from more than 300,000 words and phrases.</li>
    <li>Multiple usages to clarify the context.</li>
    <li>Audio, phonetics, meanings, synonyms and antonyms</li>
    <li>Save the words to your personal deck and access from anywhere</li>
  </ul>
  <div class="dots"><span></span><span></span><span></span><span></span></div>
</section>

<div class="browse">
  <b>Browse Dictionary :</b>
  <div class="letters">
    <span class="on">A</span><span>B</span><span>C</span><span>D</span><span>E</span><span>F</span><span>G</span><span>H</span><span>I</span><span>J</span><span>K</span><span>L</span><span>M</span><span>N</span><span>O</span><span>P</span><span>Q</span><span>R</span><span>S</span><span>T</span><span>U</span><span>V</span><span>W</span><span>X</span><span>Y</span><span>Z</span>
  </div>
</div>

<section class="crossword" role="img" aria-label="Photo of a pencil on a crossword grid">
  <h2>DAILY CROSSWORD</h2>
  <p>Take this daily crossword challenge from Lumo Wordfind.</p>
  <div class="btn">SOLVE NOW</div>
</section>

<aside class="tidbit">
  <h3>ENGLISH TIDBIT</h3>
  <div class="word">gaffe/gaf</div>
  <p>"Gaffe" is a social blunder and "gaff" is a large hook. Be warned not to make the gaffe of mixing it up with gaff.</p>
  <div class="arrows"><b>&lsaquo;</b> &rsaquo;</div>
  <footer><span>Gantlet / gauntlet</span><span>Theater / theatre</span></footer>
</aside>

<section class="addon">
  <h2>EMBERFOX ADDON</h2>
  <h4>Quick Dictionary Lookup from LumoWordfind.com</h4>
  <p>Add this tool to your Emberfox and quickly look up for definitions from any website without leaving the page.</p>
  <div class="btn">GET IT NOW</div>
  <div class="press"><b>JUST PRESS</b><span>SHIFT + click</span></div>
</section>

<section class="mobile" role="img" aria-label="Photo of books with a hand holding a phone showing the app">
  <div class="text">
    <h2>DESIGNED FOR NIMBUS PHONE</h2>
    <p>Lumo Wordfind is specially designed for your Nimbus phone to quickly lookup meaining, usages and audio of words.</p>
    <div class="store"></div>
  </div>
  <div class="phone"></div>
</section>

<footer class="footer">
  <nav><span>FAQ</span><span>Contact</span><span>BlogLegal</span><span>Privacy Policy</span><span>Terms of UseOthers</span><span>Popular Words</span><span>Common Errors in English</span><span>TestPrep Online</span></nav>
  <p>Copyright © 2016 lumowordfind.com. All rights reserved.</p>
</footer>
</body>
</html>
```